Website Design for R W Builders: Showcasing Excellence in General Contracting

R W Builders, a leading general contractor based in California, is seeking a professional and engaging website design to effectively showcase our expertise, services, and commitment to excellence. The website will serve as a digital platform to represent our brand identity, highlight our portfolio, and attract potential clients in various sectors.

Key Objectives:

Reflect Company Identity: The website should accurately reflect the identity and values of R W Builders, including our dedication to quality, professionalism, and client satisfaction.
Showcase Services: Highlight our wide range of general contracting services, including but not limited to construction management, design-build, renovation, and commercial construction.
Portfolio Display: Display an extensive portfolio of past projects completed by R W Builders, showcasing our capabilities, craftsmanship, and successful outcomes.
Client Testimonials: Incorporate client testimonials and case studies to demonstrate our track record of delivering projects on time, within budget, and to the highest standards.
Contact Information: Ensure easy access to contact information, including phone number, email, and physical address, to facilitate communication with potential clients.
Responsive Design: Develop a responsive website design optimized for various devices and screen sizes, ensuring a seamless user experience across desktops, laptops, tablets, and smartphones.
Search Engine Optimization (SEO): Implement SEO best practices to enhance the visibility of the website on search engines, increasing organic traffic and generating leads.
User-Friendly Navigation: Create an intuitive and user-friendly navigation structure that enables visitors to easily find the information they need, such as services, portfolio, testimonials, and contact details.
Visual Appeal: Utilize visually appealing graphics, images, and layout designs to capture the attention of visitors and leave a lasting impression of professionalism and quality.
Compliance and Security: Ensure compliance with industry standards and regulations, as well as implementing necessary security measures to protect user data and privacy.

```html
<!DOCTYPE html>
<html lang="en">
<head>
<meta charset="utf-8">
<title>R W Builders — General Contracting</title>
<link href="https://fonts.googleapis.com/css2?family=Oswald:wght@500;600;700&family=Roboto:wght@400;500;700&display=swap" rel="stylesheet">
<style>
:root{
  --navy:#2a2867;
  --navy-deep:#1f1d55;
  --blue:#0b8ed8;
  --blue-bright:#1aa3ec;
  --ink:#1a1a1a;
  --text:#444;
  --muted:#888;
  --light:#f4f4f5;
  --white:#fff;
  --footer:#111114;
  --footer-bar:#0a0a0c;
}
*{box-sizing:border-box;margin:0;padding:0}
html,body{width:1200px;height:4238px;overflow:hidden}
body{position:relative;font-family:"Roboto",Arial,sans-serif;color:var(--ink);background:var(--white)}
.abs{position:absolute}
.heading{font-family:"Oswald","Arial Narrow",sans-serif;font-weight:600;font-size:52px;letter-spacing:.5px;text-align:center;left:0;width:1200px;color:var(--ink)}
.heading::after{content:"";display:block;width:76px;height:4px;background:var(--blue);margin:4px auto 0}
.heading.light{color:var(--white)}
.heading.light::after{background:var(--white)}

/* header */
.site-header{top:0;left:0;width:1200px;height:128px;background:var(--white)}
.brand{left:108px;top:24px;width:90px;text-align:center}
.brand-mark{width:34px;height:34px;background:var(--ink);margin:0 auto 6px}
.brand-name{font-weight:700;font-size:12px;color:var(--ink);line-height:1.2}
.brand-place{font-weight:700;font-size:8px;color:var(--ink);margin-top:2px}
.main-nav{left:268px;top:57px;display:flex;gap:27px;font-size:14px;font-weight:500;color:var(--ink)}
.main-nav .active{color:var(--blue)}
.social{display:flex;gap:6px}
.social span{width:32px;height:32px;border-radius:50%;border:2px solid #b9d8ee;display:block}
.social span:first-child{background:var(--navy);border-color:var(--navy)}
.header-social{left:782px;top:50px}
.call-panel{left:908px;top:0;width:292px;height:128px}
.call-icon{left:1017px;top:28px;width:38px;height:38px;border-radius:50%;background:var(--blue)}
.call-label{left:1072px;top:39px;font-size:11px;font-weight:700;color:var(--white)}
.call-number{left:970px;top:72px;font-size:28px;font-weight:500;color:var(--white)}

/* hero */
.hero{top:128px;left:0;width:1200px;height:618px;background:linear-gradient(100deg,#6b6f78 0%,#9a8f84 40%,#b9a78e 62%,#6f7a5c 100%)}
.hero-shade{top:128px;left:0;width:1200px;height:618px;background:linear-gradient(90deg,rgba(20,22,30,.55),rgba(20,22,30,.1) 60%,rgba(0,0,0,0))}
.hero-kicker{left:111px;top:324px;font-family:"Oswald",sans-serif;font-weight:500;font-size:20px;color:var(--white)}
.hero-title{left:111px;top:348px;font-family:"Oswald",sans-serif;font-weight:600;font-size:46px;color:var(--white);letter-spacing:.5px}
.hero-text{left:111px;top:416px;width:480px;font-size:19px;line-height:30px;color:var(--white)}
.btn{display:flex;align-items:center;justify-content:center;font-weight:700;color:var(--white);background:linear-gradient(90deg,var(--navy),var(--blue));font-size:14px}
.hero-btn{left:111px;top:500px;width:145px;height:46px}

/* experience */
.experience{top:746px;left:0;width:1200px;height:501px;background:var(--light)}
.exp-title{top:836px}
.exp-text{left:190px;top:928px;width:820px;font-size:15px;line-height:27px;text-align:center;color:var(--text)}
.feature{width:177px;height:145px;top:1046px;background:var(--white);box-shadow:0 6px 14px rgba(0,0,0,.1);text-align:center;font-size:13px;line-height:21px;color:#333;padding-top:96px}
.feature svg{position:absolute;left:60px;top:20px}

/* services */
.svc-title{top:1392px}
.tab{top:1497px;width:229px;height:48px;font-size:14px;font-weight:700;display:flex;align-items:center;justify-content:center}
.tab.outline{left:365px;border:1px solid var(--blue);color:var(--navy);background:var(--white)}
.tab.filled{left:605px;background:var(--navy);color:var(--white)}
.svc-card{top:1590px;width:290px;height:348px;clip-path:polygon(50% 0,100% 50px,100% 100%,0 100%,0 50px)}
.svc-photo{background:linear-gradient(160deg,#9c8f80,#6d6a63 55%,#5c4f3c)}
.svc-active{background:linear-gradient(160deg,var(--navy),#1665b0 60%,var(--blue))}
.svc-label{left:0;width:290px;text-align:center;top:298px;font-size:17px;font-weight:700;color:var(--white)}
.svc-label::after{content:"";display:block;width:36px;height:3px;background:var(--white);margin:7px auto 0}
.svc-active .t{top:132px;left:0;width:290px;text-align:center;font-size:18px;font-weight:700;color:var(--white)}
.svc-active .d{top:178px;left:25px;width:240px;text-align:center;font-size:14px;line-height:24px;color:var(--white)}
.svc-active .more{top:269px;left:86px;width:117px;height:38px;background:var(--white);color:var(--navy);font-size:12px;font-weight:700;display:flex;align-items:center;justify-content:center}
.arrow-btn{top:1743px;width:42px;height:42px;background:var(--white);display:flex;align-items:center;justify-content:center}

/* testimonials */
.test-title{top:2047px}
.avatar{width:136px;height:136px;border-radius:50%;border:5px solid var(--white);box-shadow:0 4px 14px rgba(0,0,0,.25);background:linear-gradient(160deg,#e8e8e8,#bdbdbd)}
.quote{width:30px;height:30px;border-radius:50%;background:var(--white);box-shadow:0 2px 6px rgba(0,0,0,.2);color:var(--blue);font-weight:700;font-size:16px;display:flex;align-items:center;justify-content:center}
.t-name{font-size:17px;font-weight:700;color:var(--navy)}
.t-name small{font-size:14px;font-weight:500;color:#333}
.t-text{width:310px;font-size:14px;line-height:25px;color:var(--muted)}
.dots{left:562px;top:2350px;display:flex;gap:9px}
.dots span{width:11px;height:11px;border-radius:50%;background:#b3b8c8}
.dots span.on{background:var(--blue)}

/* portfolio */
.portfolio{top:2455px;left:0;width:1200px;height:788px;background:linear-gradient(110deg,var(--navy-deep) 0%,#1e4e9a 55%,var(--blue) 100%)}
.port-title{top:2522px}
.shot{box-shadow:0 4px 12px rgba(0,0,0,.25)}

/* contact */
.contact-title{top:3354px}
.info-icon{width:60px;height:60px;border-radius:50%;background:var(--white);box-shadow:0 4px 12px rgba(0,0,0,.12);display:flex;align-items:center;justify-content:center}
.info-label{font-size:14px;font-weight:700;color:var(--navy)}
.info-value{font-size:14px;line-height:21px;color:#333;margin-top:6px}
.field{background:var(--white);box-shadow:0 3px 12px rgba(0,0,0,.1);font-size:14px;color:#555;padding:16px 17px}
.send-btn{left:519px;top:3733px;width:162px;height:48px}

/* footer */
.site-footer{top:3890px;left:0;width:1200px;height:300px;background:var(--footer)}
.f-divider{top:3890px;width:1px;height:300px;background:#2a2a30}
.f-head{font-size:16px;font-weight:700;color:var(--white);padding-left:24px;border-left:3px solid var(--navy);line-height:30px}
.f-list{list-style:none;font-size:14px;color:#e6e6e6}
.f-list li{display:flex;align-items:center;gap:14px;height:40px}
.f-list li::before{content:"";width:13px;height:13px;border-radius:50%;background:var(--blue)}
.f-info{font-size:13px;line-height:19px;color:#ddd}
.f-info b{display:block;font-size:14px;color:var(--white)}
.foot-brand{left:150px;top:3985px;width:130px;text-align:center}
.foot-brand .brand-mark{width:40px;height:40px;background:var(--white)}
.foot-brand .brand-name{color:var(--white);font-size:15px}
.foot-brand .brand-place{color:var(--white);font-size:10px}
.footer-bar{top:4190px;left:0;width:1200px;height:48px;background:var(--footer-bar);font-size:11px;color:#ddd}
</style>
</head>
<body>

<header class="abs site-header">
  <div class="abs brand">
    <div class="brand-mark"></div>
    <div class="brand-name">R W BUILDERS</div>
    <div class="brand-place">ARROYO VALE, CA</div>
  </div>
  <nav class="abs main-nav">
    <span class="active">HOME</span><span>ABOUT US</span><span>SERVICES</span><span>PORTFOLIO</span><span>CONTACT US</span>
  </nav>
  <div class="abs social header-social" aria-label="Social links"><span></span><span></span><span></span></div>
  <svg class="abs call-panel" width="292" height="128" viewBox="0 0 292 128"><polygon points="0,128 80,0 292,0 292,128" fill="var(--navy)"/></svg>
  <div class="abs call-icon">
    <svg width="38" height="38" viewBox="0 0 38 38"><path d="M14 11c1 0 2 3 2.5 4.5.3 1-1.3 1.8-1.3 2.5.6 2 2.8 4.3 4.8 5 .8 0 1.5-1.6 2.5-1.3 1.5.5 4.5 1.5 4.5 2.5 0 2-2 4-4 4-7 0-13-6-13-13 0-2 2-4 4-4z" fill="#fff"/></svg>
  </div>
  <div class="abs call-label">CALL US TODAY!</div>
  <div class="abs call-number">(555) 418 - 2093</div>
</header>

<section>
  <div class="abs hero" role="img" aria-label="Photo: site engineer in hard hat and safety vest reviewing plans at a building frame under construction"></div>
  <div class="abs hero-shade"></div>
  <div class="abs hero-kicker">WELCOME TO</div>
  <h1 class="abs hero-title">R W BUILDERS</h1>
  <p class="abs hero-text">R W Builders has the ability to self-perform a wide range of civil and architectural work</p>
  <div class="abs btn hero-btn">GET STARTED</div>
</section>

<section>
  <div class="abs experience"></div>
  <h2 class="abs heading exp-title">EXPERIENCE</h2>
  <p class="abs exp-text">With vast experience in the trades, site superintendence, safety, quality control, and all aspects of general contracting, R W Builders can plan, manage and execute building construction projects in all sizes under any delivery method: design-build, CM at Risk, or design-bid-build.</p>
  <div class="abs feature" style="left:111px"><svg width="58" height="58" viewBox="0 0 58 58"><circle cx="29" cy="29" r="16" fill="none" stroke="var(--blue)" stroke-width="4" stroke-dasharray="6 4"/><circle cx="29" cy="29" r="7" fill="var(--navy)"/></svg>Quickly Mobilize<br>Assets + Personnel</div>
  <div class="abs feature" style="left:311px"><svg width="58" height="58" viewBox="0 0 58 58"><circle cx="29" cy="24" r="16" fill="var(--blue)"/><circle cx="29" cy="24" r="9" fill="#fff"/><path d="M20 38l-4 14 8-4 5 6 3-14zM38 38l4 14-8-4-5 6-3-14z" fill="var(--navy)"/></svg>Commitment to<br>Quality + Safety</div>
  <div class="abs feature" style="left:511px"><svg width="58" height="58" viewBox="0 0 58 58"><circle cx="30" cy="24" r="14" fill="none" stroke="var(--blue)" stroke-width="4"/><rect x="24" y="38" width="12" height="10" fill="var(--navy)"/><path d="M30 16v16M22 24h16" stroke="var(--navy)" stroke-width="3"/></svg>Complete Projects<br>on Time + on Budget</div>
  <div class="abs feature" style="left:711px"><svg width="58" height="58" viewBox="0 0 58 58"><circle cx="29" cy="16" r="7" fill="var(--blue)"/><circle cx="15" cy="22" r="6" fill="var(--navy)"/><circle cx="43" cy="22" r="6" fill="var(--navy)"/><path d="M17 46c0-10 5-16 12-16s12 6 12 16z" fill="var(--blue)"/><path d="M5 44c0-8 4-13 10-13 3 0 5 1 6 3l-4 10zM53 44c0-8-4-13-10-13-3 0-5 1-6 3l4 10z" fill="var(--navy)"/></svg>Qualified Field +<br>Office Staff</div>
  <div class="abs feature" style="left:911px"><svg width="58" height="58" viewBox="0 0 58 58"><path d="M9 28c0-11 9-19 20-19s20 8 20 19z" fill="var(--blue)"/><rect x="6" y="28" width="46" height="5" fill="var(--navy)"/><circle cx="29" cy="44" r="9" fill="none" stroke="var(--blue)" stroke-width="5"/></svg>Value<br>Engineering</div>
</section>

<section>
  <h2 class="abs heading svc-title">OUR SERVICES</h2>
  <div class="abs tab outline">SPECIALIZED SERVICES</div>
  <div class="abs tab filled">GENERAL CONTRACTING</div>

  <div class="abs svc-card svc-photo" style="left:0" role="img" aria-label="Photo: construction team in safety gear meeting on site">
    <div class="abs svc-label">PRECONSTRUCTION</div>
  </div>
  <div class="abs svc-card svc-active" style="left:303px">
    <svg class="abs" style="left:119px;top:56px" width="52" height="52" viewBox="0 0 52 52"><circle cx="20" cy="18" r="9" fill="none" stroke="#fff" stroke-width="4"/><path d="M20 27v18M14 45h12" stroke="#fff" stroke-width="4"/><path d="M32 32h14M32 38h14M32 44h14" stroke="#fff" stroke-width="3"/></svg>
    <div class="abs t">DESIGN-BUILD</div>
    <div class="abs d">Design-Build. A team working together from start to finish in open communication</div>
    <div class="abs more">LEARN MORE</div>
  </div>
  <div class="abs svc-card svc-photo" style="left:607px;background:linear-gradient(160deg,#a7a39a,#7b7566 55%,#5f6a3c)" role="img" aria-label="Photo: inspectors in hard hats reviewing a new house build">
    <svg class="abs" style="left:121px;top:228px" width="48" height="48" viewBox="0 0 48 48"><circle cx="24" cy="24" r="17" fill="none" stroke="#fff" stroke-width="6" stroke-dasharray="5 3"/><circle cx="24" cy="24" r="11" fill="#fff"/><path d="M18 24l4 4 8-8" fill="none" stroke="#555" stroke-width="3"/></svg>
    <div class="abs svc-label">QUALITY CONTROL</div>
  </div>
  <div class="abs svc-card svc-photo" style="left:911px;background:linear-gradient(160deg,#c0b49a,#8c7f66 55%,#4f4a3a)" role="img" aria-label="Photo: project managers overlooking a construction site at sunset">
    <svg class="abs" style="left:121px;top:228px" width="48" height="48" viewBox="0 0 48 48"><circle cx="20" cy="22" r="15" fill="none" stroke="#fff" stroke-width="6" stroke-dasharray="5 3"/><rect x="26" y="28" width="18" height="14" fill="#fff"/></svg>
    <div class="abs svc-label">PROJECT MANAGEMENT</div>
  </div>
  <div class="abs arrow-btn" style="left:0"><svg width="14" height="18" viewBox="0 0 14 18"><path d="M10 2L3 9l7 7" fill="none" stroke="#222" stroke-width="2.5"/></svg></div>
  <div class="abs arrow-btn" style="left:1158px"><svg width="14" height="18" viewBox="0 0 14 18"><path d="M4 2l7 7-7 7" fill="none" stroke="#222" stroke-width="2.5"/></svg></div>
</section>

<section>
  <h2 class="abs heading test-title">TESTIMONIALS</h2>
  <div class="abs avatar" style="left:113px;top:2168px" role="img" aria-label="Client portrait"></div>
  <div class="abs quote" style="left:220px;top:2168px">&ldquo;</div>
  <div class="abs t-name" style="left:286px;top:2182px">DANIEL MARSH, <small>California</small></div>
  <p class="abs t-text" style="left:286px;top:2216px">Sed ut perspiciatis unde omnis iste natus error sit voluptatem accusantium doloremque lauda ntium, totam rem aperiamea.</p>
  <div class="abs avatar" style="left:613px;top:2168px" role="img" aria-label="Client portrait"></div>
  <div class="abs quote" style="left:720px;top:2168px">&ldquo;</div>
  <div class="abs t-name" style="left:786px;top:2182px">RENATA, <small>California</small></div>
  <p class="abs t-text" style="left:786px;top:2216px">Sed ut perspiciatis unde omnis iste natus error sit voluptatem accusantium doloremque lauda ntium, totam rem aperiamea.</p>
  <div class="abs dots"><span></span><span class="on"></span><span></span><span></span></div>
</section>

<section>
  <div class="abs portfolio"></div>
  <h2 class="abs heading light port-title">OUR PORTFOLIO</h2>
  <div class="abs shot" style="left:111px;top:2632px;width:480px;height:282px;background:linear-gradient(180deg,#e0a85a,#8f7a5a 55%,#4d4536)" role="img" aria-label="Photo: two workers watching cranes over a city site at sunrise"></div>
  <div class="abs shot" style="left:609px;top:2632px;width:480px;height:282px;background:linear-gradient(180deg,#b9b59b,#a69a7e 55%,#8e7c62)" role="img" aria-label="Photo: crew breaking ground with shovels at a groundbreaking event"></div>
  <div class="abs shot" style="left:111px;top:2930px;width:315px;height:231px;background:linear-gradient(180deg,#5a7fb0,#e6a244 60%,#8a5a2a)" role="img" aria-label="Photo: building scaffold and crane against a sunset sky"></div>
  <div class="abs shot" style="left:442px;top:2930px;width:315px;height:231px;background:linear-gradient(160deg,#8c8a86,#c8a272 55%,#a47a48)" role="img" aria-label="Photo: aerial view of a timber floor interior under construction"></div>
  <div class="abs shot" style="left:773px;top:2930px;width:316px;height:231px;background:linear-gradient(160deg,#dfe4e8,#a9b4be 55%,#5d6670)" role="img" aria-label="Photo: engineer using a tablet over blueprints with a hard hat"></div>
</section>

<section>
  <h2 class="abs heading contact-title">CONTACT US</h2>
  <div class="abs info-icon" style="left:244px;top:3470px"><svg width="26" height="28" viewBox="0 0 26 28"><path d="M13 2a8 8 0 0 0-8 8c0 6 8 13 8 13s8-7 8-13a8 8 0 0 0-8-8z" fill="var(--navy)"/><circle cx="13" cy="10" r="3" fill="#fff"/><ellipse cx="13" cy="25" rx="9" ry="2" fill="none" stroke="var(--blue)" stroke-width="2"/></svg></div>
  <div class="abs" style="left:329px;top:3463px"><div class="info-label">LOCATION:</div><div class="info-value">P.O. Box 2210 Arroyo Vale,<br>CA 93520</div></div>
  <div class="abs info-icon" style="left:512px;top:3470px"><svg width="26" height="26" viewBox="0 0 26 26"><path d="M7 3c1 0 2 3 2.5 4.5.3 1-1.3 1.8-1.3 2.5.6 2 2.8 4.3 4.8 5 .8 0 1.5-1.6 2.5-1.3 1.5.5 4.5 1.5 4.5 2.5 0 2-2 4-4 4C9 20 3 14 3 7c0-2 2-4 4-4z" fill="var(--navy)"/><path d="M15 4a8 8 0 0 1 7 7" fill="none" stroke="var(--blue)" stroke-width="2"/></svg></div>
  <div class="abs" style="left:598px;top:3475px"><div class="info-label">CALL US:</div><div class="info-value" style="margin-top:12px">(555) 418-2093</div></div>
  <div class="abs info-icon" style="left:737px;top:3470px"><svg width="28" height="22" viewBox="0 0 28 22"><rect x="2" y="3" width="22" height="16" fill="var(--navy)"/><path d="M2 3l11 9 11-9" fill="none" stroke="#fff" stroke-width="2"/><circle cx="23" cy="16" r="5" fill="var(--blue)"/></svg></div>
  <div class="abs" style="left:822px;top:3475px"><div class="info-label">EMAIL US:</div><div class="info-value" style="margin-top:12px">info@rwbuilders.example</div></div>

  <div class="abs field" style="left:165px;top:3562px;width:283px;height:48px">Full Name</div>
  <div class="abs field" style="left:458px;top:3562px;width:283px;height:48px">Phone</div>
  <div class="abs field" style="left:751px;top:3562px;width:283px;height:48px">Email Address</div>
  <div class="abs field" style="left:165px;top:3622px;width:869px;height:94px">Message</div>
  <div class="abs btn send-btn">SEND MESSAGE</div>
</section>

<footer>
  <div class="abs site-footer"></div>
  <div class="abs foot-brand">
    <div class="brand-mark"></div>
    <div class="brand-name">R W BUILDERS</div>
    <div class="brand-place">ARROYO VALE, CA</div>
  </div>
  <div class="abs f-divider" style="left:360px"></div>
  <div class="abs f-divider" style="left:585px"></div>
  <div class="abs f-divider" style="left:848px"></div>
  <div class="abs f-head" style="left:362px;top:3928px">NAVIGATION</div>
  <ul class="abs f-list" style="left:386px;top:3970px"><li>Home</li><li>About Us</li><li>Services</li><li>Portfolio</li><li>Contact Us</li></ul>
  <div class="abs f-head" style="left:587px;top:3928px">QUICK LINKS</div>
  <ul class="abs f-list" style="left:611px;top:3970px"><li>Site Map</li><li>Privacy Policy</li><li>Terms Of Use</li><li>Disclaimer</li></ul>
  <div class="abs f-head" style="left:850px;top:3928px">CONTACT INFO</div>
  <div class="abs f-info" style="left:925px;top:3978px"><b>LOCATION:</b>P.O. Box 2210 Arroyo Vale,<br>CA 93520</div>
  <div class="abs f-info" style="left:925px;top:4066px"><b>PHONE:</b>(555) 418-2093</div>
  <div class="abs f-info" style="left:925px;top:4124px"><b>EMAIL:</b>info@rwbuilders.example</div>
  <svg class="abs" style="left:890px;top:3980px" width="14" height="170" viewBox="0 0 14 170"><path d="M7 0a5 5 0 0 0-5 5c0 4 5 9 5 9s5-5 5-9a5 5 0 0 0-5-5z" fill="var(--blue)"/><path d="M3 88c1 0 2 2 2 3 0 1-1 1-1 2 1 2 2 3 4 4 1 0 1-1 2-1s3 1 3 2c0 1-1 3-3 3-5 0-9-4-9-9 0-2 1-4 2-4z" fill="var(--blue)"/><rect x="0" y="148" width="14" height="10" fill="var(--blue)"/></svg>

  <div class="abs footer-bar">
    <div class="abs" style="left:111px;top:18px">CA Contractor License: 574318 A+B</div>
    <div class="abs" style="left:460px;top:18px">© 2024 / R W BUILDERS &nbsp;&nbsp;| &nbsp;&nbsp;All Rights Reserved</div>
    <div class="abs social" style="left:938px;top:8px" aria-label="Social links"><span></span><span style="background:#fff;border-color:#fff"></span><span style="background:var(--navy);border-color:var(--navy)"></span></div>
  </div>
</footer>

</body>
</html>
```